KAJU Freightways #ALLKAJU Business Cards & Letterhead

I am looking to business cards designed for our organization. We are currently undergoing a small re-branding that is taking place. Our organization is called KAJU Freightways and we are headquartered in Phoenix, AZ. We primarily provide transportation and logistics services to the Marlow Parcel Bureau who is our largest customer. I would like to see a design that incorporates name, title, contact info, website, and address (this will be different depending on the employee). I would also like to see some color on the business card using our logo colors or a variation. I would like our logo on the back of the business card with the website displayed. The final design should communicate that we are a next generation transportation operate that focuses on being driver-first, customer-centric, innovative, and sustainable.We would also like our #ALLKAJU catch phrase incorporated as well.

Target Market(s)

Transportation & Logistics

Industry/Entity Type

Trucking Company

Contact Information for Business Card

-First and Last Name
-Position Title
-Contact Phone
-Contact Email
-Physical Address

Font styles to use
Serif

Colors

Designer to choose colors to be used in the design.

Requirements
Must have
• -KAJU logo prominently displayed
• -#ALLKAJU catch phrase used
• -Some amount of color, design gradient, etc.
• -Logo on the back with website listed (https://www.kajufreightco.example)

```html
<!DOCTYPE html>
<html lang="en">
<head>
<meta charset="utf-8">
<title>KAJU Freightways Business Card</title>
<link rel="stylesheet" href="https://fonts.googleapis.com/css2?family=Roboto:wght@400;700&display=swap">
<style>
  :root {
    --bg: #7a7a7a;
    --green: #84c441;
    --navy: #0f3a45;
    --ink: #555555;
    --rule: #8a8a8a;
    --white: #ffffff;
  }
  html, body {
    margin: 0;
    padding: 0;
    width: 1200px;
    height: 675px;
    overflow: hidden;
    background: var(--bg);
    font-family: "Roboto", Arial, sans-serif;
  }
  .stage {
    position: relative;
    width: 1200px;
    height: 675px;
  }
  .card {
    position: absolute;
    top: 188px;
    width: 525px;
    height: 300px;
    border-radius: 16px;
    box-shadow: 0 4px 14px rgba(0,0,0,0.3);
    overflow: hidden;
  }
  .card-back {
    left: 50px;
    background: var(--green);
  }
  .card-front {
    left: 625px;
    background: var(--white);
  }
  .wordmark {
    position: absolute;
    display: flex;
    align-items: center;
    gap: 12px;
    font-weight: 700;
    letter-spacing: 1px;
  }
  .wordmark .dot {
    border-radius: 50%;
    display: block;
  }
  .card-back .wordmark {
    left: 0; right: 0; top: 96px;
    justify-content: center;
    color: var(--white);
    font-size: 60px;
  }
  .card-back .wordmark .dot {
    width: 26px; height: 26px;
    border: 5px solid var(--white);
  }
  .card-back .website {
    position: absolute;
    left: 0; right: 0; bottom: 44px;
    text-align: center;
    color: var(--white);
    font-size: 15px;
  }
  .card-front .wordmark {
    right: 34px; top: 34px;
    color: var(--navy);
    font-size: 40px;
  }
  .card-front .wordmark .dot {
    width: 18px; height: 18px;
    border: 4px solid var(--green);
  }
  .hashtag {
    position: absolute;
    right: 36px; top: 88px;
    font-size: 12px;
    color: var(--ink);
  }
  .divider {
    position: absolute;
    left: 140px; right: 30px; top: 128px;
    border-top: 1px solid var(--rule);
  }
  .address {
    position: absolute;
    right: 34px; top: 140px;
    text-align: right;
    font-size: 13px;
    line-height: 1.35;
    color: var(--ink);
  }
  .person {
    position: absolute;
    left: 34px; top: 170px;
  }
  .person .name {
    color: var(--green);
    font-weight: 700;
    font-size: 22px;
    letter-spacing: 0.5px;
  }
  .person .title {
    color: var(--navy);
    font-size: 16px;
    margin-top: 2px;
    padding-bottom: 6px;
    border-bottom: 1px solid var(--rule);
    width: 150px;
  }
  .contacts {
    list-style: none;
    margin: 8px 0 0;
    padding: 0;
    font-size: 14px;
    color: var(--ink);
  }
  .contacts li {
    display: flex;
    align-items: center;
    gap: 7px;
    line-height: 1.45;
  }
  .contacts svg { width: 12px; height: 12px; }
</style>
</head>
<body>
<div class="stage">
  <section class="card card-back">
    <div class="wordmark"><span class="dot"></span>KAJU</div>
    <div class="website">www.kajufreightco.example</div>
  </section>

  <section class="card card-front">
    <div class="wordmark"><span class="dot"></span>KAJU</div>
    <div class="hashtag">#ALLKAJU</div>
    <div class="divider"></div>
    <div class="address">4170 North Cedar<br>Ridge Road Mesa<br>AZ 85201</div>

    <div class="person">
      <div class="name">RENA ALCOTT</div>
      <div class="title">President</div>
      <ul class="contacts">
        <li>
          <svg viewBox="0 0 12 12"><path d="M2.5 1 L4.5 1 L5 3.5 L3.8 4.5 Q5 7 7.5 8.2 L8.5 7 L11 7.5 L11 9.5 Q10.5 11 9 11 Q1 10 1 2.5 Q1 1 2.5 1 Z" fill="var(--green)"/></svg>
          480-555-0142
        </li>
        <li>
          <svg viewBox="0 0 12 12"><rect x="0.5" y="2" width="11" height="8" fill="var(--green)"/><path d="M0.5 2 L6 6.5 L11.5 2" stroke="#fff" fill="none" stroke-width="1"/></svg>
          info@kajufreightco.example
        </li>
        <li>
          <svg viewBox="0 0 12 12"><circle cx="6" cy="6" r="5" fill="none" stroke="var(--green)" stroke-width="1.2"/><ellipse cx="6" cy="6" rx="2.2" ry="5" fill="none" stroke="var(--green)" stroke-width="1"/><line x1="1" y1="6" x2="11" y2="6" stroke="var(--green)" stroke-width="1"/></svg>
          www.kajufreightco.example
        </li>
      </ul>
    </div>
  </section>
</div>
</body>
</html>
```